Luxury WordPress Website for CORALBASINS

I need a professional WordPress website for Coral Basins. The site should be modern, visually appealing, and user-friendly, reflecting the brand’s luxury and premium identity. It must include a homepage, product/service pages, contact form, and be responsive on both desktop and mobile devices. The design should allow for easy updates and integration of future content, while maintaining a polished and professional look.

Target Market(s)

swimmingpool & spa

Industry/Entity Type

Swimmingpool

Coding

Coded - Design and coding required

Font styles to use
Other font styles liked:
• HaboroSoft

Requirements
Must have
• Exclusive appearance
Nice to have
• • A logo that subtly incorporates water or pool elements. • A color palette that reflects luxury, elegance, and relaxation. • Clean and modern typography that is easy to read across all media. • Iconography or design elements that convey premium quality. • A versatile design that can be adapted for social media, merchandise, and promotional materials. • Optional: A tagline that emphasizes luxury and high-end pool experiences.

```html
<!DOCTYPE html>
<html lang="en">
<head>
<meta charset="utf-8">
<title>Coral Basins — Luxury Pools</title>
<link href="https://fonts.googleapis.com/css2?family=Ubuntu:wght@400;500;700&family=Montserrat:wght@400;500;600;700&display=swap" rel="stylesheet">
<style>
:root{
  --navy:#0d2c54;
  --blue:#1d72d0;
  --sky:#2a8ee0;
  --label:#1e88e5;
  --pale:#d3effc;
  --yellow:#f4d82a;
  --white:#ffffff;
  --text:#1f2a36;
  --muted:#3a4450;
  --deep:#0f3766;
  --green:#8cc63f;
}
*{margin:0;padding:0;box-sizing:border-box}
html,body{width:1200px;height:4231px;overflow:hidden}
body{position:relative;background:var(--white);font-family:'Montserrat',sans-serif;color:var(--text)}
.abs{position:absolute}
.head{font-family:'Ubuntu',sans-serif;font-weight:500;color:var(--navy);letter-spacing:.3px}
.center{left:0;width:1200px;text-align:center}
.eyebrow{font-size:14px;font-weight:600;color:var(--label)}

/* header */
.brand-dot{left:118px;top:8px;width:66px;height:66px;border-radius:50%;background:var(--blue)}
.brand-name{left:198px;top:15px;font-size:23px;font-family:'Ubuntu',sans-serif;font-weight:500;color:var(--navy)}
.brand-tag{left:200px;top:46px;font-size:11.5px;font-weight:500;color:var(--navy)}
.nav{top:32px;font-size:12.5px;font-weight:500;color:var(--navy)}
.nav span{margin:0 14px}
.nav .current{text-decoration:underline;font-weight:700}
.phone{left:948px;top:28px;font-size:17px;font-weight:700;color:var(--navy)}

/* hero */
.hero{left:0;top:79px;width:1200px;height:561px;background:linear-gradient(180deg,#3c3e57 0%,#c0573e 18%,#6e4a45 32%,#2d3a4c 52%,#1b4f7c 72%,#1f6aa5 100%)}
.hero-l1{left:118px;top:167px;font-size:45px;color:var(--yellow)}
.hero-l2{left:118px;top:218px;font-size:57px;color:var(--white)}
.hero-p{left:119px;top:296px;font-size:15.5px;line-height:27px;color:var(--white)}
.btn{display:flex;align-items:center;justify-content:center;border-radius:22px;font-size:13.5px;font-weight:700}
.btn-yellow{background:var(--yellow);color:var(--navy)}
.btn-navy{background:var(--navy);color:var(--white)}

/* services */
.card{background:var(--white);border-radius:8px;box-shadow:0 3px 10px rgba(0,0,0,.18)}
.card-img{left:6px;top:6px;right:6px;height:188px;border-radius:4px}
.card-icon{width:78px;height:78px;border-radius:50%;background:var(--sky);border:4px solid var(--white);top:148px;left:calc(50% - 39px)}
.card-title{top:238px;width:100%;text-align:center;font-size:18px;font-weight:700;color:var(--text)}
.card-text{top:278px;left:14px;right:14px;text-align:center;font-size:13px;line-height:24px;color:var(--muted)}
.card-more{top:360px;width:100%;text-align:center;font-size:13px;font-weight:700;color:var(--navy)}
.arrow{width:36px;height:36px}

/* about */
.about-p{left:620px;top:1582px;width:393px;font-size:13.6px;line-height:24.2px;text-align:justify;color:var(--text)}

/* stats */
.stat{width:240px;text-align:center}
.stat-ic{width:86px;height:86px;border-radius:50%;background:var(--yellow);margin:0 auto}
.stat-num{font-family:'Ubuntu',sans-serif;font-weight:500;font-size:35px;color:var(--yellow);margin-top:12px}
.stat-bar{width:34px;height:3px;background:var(--white);margin:8px auto 0}
.stat-label{font-size:17px;font-weight:700;color:var(--white);margin-top:22px}

/* projects */
.proj-label{font-size:17px;font-weight:700;color:var(--text);text-align:center;line-height:26px}

/* testimonials */
.quote{border-radius:34px;background:var(--white);box-shadow:0 4px 10px rgba(0,0,0,.14)}
.avatar{width:142px;height:142px;border-radius:50%}
.q-name{font-size:17px;font-weight:700;color:var(--text)}
.q-text{width:290px;font-size:13px;line-height:26.5px;color:var(--muted)}

/* footer */
.f-head{font-family:'Ubuntu',sans-serif;font-weight:500;font-size:18px;color:var(--navy)}
.f-list{list-style:none;font-size:14px;color:var(--muted)}
.f-list li{height:33.5px;display:flex;align-items:center;gap:10px}
.f-contact{font-size:14px;color:var(--muted);line-height:26px}
</style>
</head>
<body>

<!-- header -->
<div class="abs brand-dot"></div>
<div class="abs brand-name">CORAL BASINS</div>
<div class="abs brand-tag">ALL YOUR DREAMS COME TRUE</div>
<nav class="abs nav" style="left:443px"><span class="current">HOME</span>|<span>ABOUT US</span>|<span>OUR PRODUCT</span>|<span>CONTACT US</span></nav>
<svg class="abs" style="left:892px;top:20px" width="46" height="40" viewBox="0 0 46 40" fill="none" stroke="#1d72d0" stroke-width="2.4" stroke-linecap="round" stroke-linejoin="round">
  <path d="M6 8c-2 3 0 10 6 17s13 11 17 10l3-4-6-5-4 3c-3-1-7-5-9-9l3-4-4-6z"/>
  <rect x="22" y="3" width="20" height="14" rx="7"/><path d="M27 17l-2 4 5-4"/>
</svg>
<div class="abs phone">+1 555 014 2290</div>

<!-- hero -->
<div class="abs hero" role="img" aria-label="Photo of an infinity pool at a desert resort at sunset, mountains behind"></div>
<svg class="abs" style="left:0;top:540px" width="1200" height="102" viewBox="0 0 1200 102" preserveAspectRatio="none">
  <path d="M0 88 C20 60 60 60 120 66 C260 80 330 20 470 40 C600 58 660 92 800 72 C930 54 1000 30 1080 46 C1140 58 1170 50 1200 40 L1200 102 L0 102Z" fill="#fff"/>
</svg>
<h1 class="abs head hero-l1">DEFINING LUXURY LIVING –</h1>
<div class="abs head hero-l2">ONE POOL AT A TIME.</div>
<p class="abs hero-p">Coral Basins creates bespoke aquatic masterpieces<br>that embody luxury, precision, and timeless elegance.</p>
<div class="abs btn btn-yellow" style="left:118px;top:372px;width:163px;height:42px">GET A QUOTE</div>

<!-- services -->
<div class="abs center eyebrow" style="top:692px">Our Services</div>
<h2 class="abs center head" style="top:718px;font-size:37px">DISCOVER OUR EXPERTISE</h2>
<p class="abs center" style="top:786px;font-size:15.5px;font-weight:500">Every pool we create is a seamless fusion of art, engineering, and individuality.</p>

<svg class="abs arrow" style="left:34px;top:1021px" viewBox="0 0 36 36" fill="none" stroke="#1d72d0" stroke-width="2"><circle cx="18" cy="18" r="16"/><path d="M26 18H11M17 12l-6 6 6 6"/></svg>
<svg class="abs arrow" style="left:1128px;top:1021px" viewBox="0 0 36 36" fill="none" stroke="#1d72d0" stroke-width="2"><circle cx="18" cy="18" r="16"/><path d="M10 18h15M19 12l6 6-6 6"/></svg>

<article class="abs card" style="left:119px;top:843px;width:311px;height:400px">
  <div class="abs card-img" style="background:linear-gradient(180deg,#2f5a2f,#3f7fa8 60%,#6d8a4f)" role="img" aria-label="Photo of a landscaped custom pool with patio furniture"></div>
  <div class="abs card-icon"></div>
  <div class="abs card-title">Luxury Custom Pools</div>
  <p class="abs card-text">Our signature offering —<br>hand-designed and precision-built pools<br>that elevate residential and resort</p>
  <div class="abs card-more">READ MORE ›</div>
</article>
<article class="abs card" style="left:444px;top:843px;width:312px;height:400px">
  <div class="abs card-img" style="background:linear-gradient(180deg,#7f9db8,#d9a979 50%,#2f5570)" role="img" aria-label="Photo of an infinity edge pool overlooking a city skyline"></div>
  <div class="abs card-icon"></div>
  <div class="abs card-title">Infinity Edge Pools</div>
  <p class="abs card-text">Experience the illusion of endless water.<br>Our infinity pools blend natural<br>landscapes and architecture</p>
  <div class="abs card-more">READ MORE ›</div>
</article>
<article class="abs card" style="left:769px;top:843px;width:312px;height:400px">
  <div class="abs card-img" style="background:linear-gradient(180deg,#4b5a66,#a9b4bc 50%,#7e8f9c)" role="img" aria-label="Photo of workers renovating an empty pool"></div>
  <div class="abs card-icon"></div>
  <div class="abs card-title">Pool Renovations</div>
  <p class="abs card-text">Transform your existing pool with<br>modern features, elegant finishes, and<br>advanced technologies</p>
  <div class="abs card-more">READ MORE ›</div>
</article>

<!-- about -->
<svg class="abs" style="left:0;top:1284px" width="1200" height="740" viewBox="0 0 1200 740" preserveAspectRatio="none">
  <path d="M0 30 C60 10 120 40 200 38 C320 34 380 62 520 50 C660 38 720 60 840 40 C960 20 1080 14 1200 4 L1200 740 L0 740Z" fill="#d3effc"/>
</svg>
<svg class="abs" style="left:0;top:1946px" width="1200" height="386" viewBox="0 0 1200 386" preserveAspectRatio="none">
  <defs><linearGradient id="bandGrad" x1="0" y1="0" x2="0" y2="1"><stop offset="0" stop-color="#1a6ec9"/><stop offset="1" stop-color="#2978cf"/></linearGradient></defs>
  <path d="M0 58 C80 60 140 46 240 40 C360 34 400 10 500 12 C620 14 660 40 780 34 C900 28 960 6 1060 10 C1120 12 1170 18 1200 14 L1200 386 L0 386Z" fill="url(#bandGrad)"/>
</svg>
<div class="abs" style="left:113px;top:1435px;width:398px;height:398px;border-radius:50%;background:linear-gradient(160deg,#3a5a6a,#2b4e7a 50%,#1d3f8c)" role="img" aria-label="Photo of a smiling pool technician in blue workwear"></div>
<div class="abs" style="left:366px;top:1678px;width:200px;height:200px;border-radius:50%;border:5px solid #fff;background:linear-gradient(160deg,#3d8fb5,#2e5f4f 60%,#3a3a3a)" role="img" aria-label="Photo of a pool worker kneeling by the poolside"></div>

<div class="abs eyebrow" style="left:623px;top:1440px;font-size:15px;color:#1e88e5">About Us</div>
<h2 class="abs head" style="left:618px;top:1470px;font-size:36px;line-height:45px">REDEFINING THE ART OF<br>LUXURY POOL DESIGN</h2>
<p class="abs about-p">Lorem Ipsum is simply dummy text of the printing and typesetting industry. Lorem Ipsum has been the industry's standard dummy text ever since the 1500s, when an unknown printer took a galley of type and scrambled it to make a type specimen book. It has survived not only five centuries, but also the leap into electronic typesetting, remaining essentially unchanged. It was popularised in the 1960s with the release of Fontrail sheets containing Lorem Ipsum passages, and more recently with desktop publishing software like Quilo</p>
<div class="abs btn btn-navy" style="left:621px;top:1850px;width:164px;height:43px">GET A QUOTE</div>

<!-- stats -->
<div class="abs stat" style="left:113px;top:2060px"><div class="stat-ic"></div><div class="stat-num">20+</div><div class="stat-bar"></div><div class="stat-label">Years of Excellence</div></div>
<div class="abs stat" style="left:355px;top:2060px"><div class="stat-ic"></div><div class="stat-num">500+</div><div class="stat-bar"></div><div class="stat-label">Prestige Projects</div></div>
<div class="abs stat" style="left:602px;top:2060px"><div class="stat-ic"></div><div class="stat-num">100%</div><div class="stat-bar"></div><div class="stat-label">Custom-Built Designs</div></div>
<div class="abs stat" style="left:846px;top:2060px"><div class="stat-ic"></div><div class="stat-num">30+</div><div class="stat-bar"></div><div class="stat-label">International Awards</div></div>

<!-- projects -->
<div class="abs center eyebrow" style="top:2429px">Our Projects</div>
<h2 class="abs center head" style="top:2455px;font-size:37px">REDEFINING LUXURY POOL DESIGN</h2>

<div class="abs" style="left:0;top:2535px;width:284px;height:255px;background:linear-gradient(180deg,#8a9bb0,#c9a99a 40%,#3c6a8a)" role="img" aria-label="Photo of a modern villa with an infinity pool"></div>
<svg class="abs" style="left:20px;top:2730px" width="244" height="62"><polygon points="0,22 244,0 244,62 0,62" fill="#fff"/></svg>
<div class="abs proj-label" style="left:20px;top:2762px;width:244px">Residential Luxury</div>

<div class="abs" style="left:302px;top:2615px;width:287px;height:255px;background:linear-gradient(180deg,#9ccde8,#3aa6d8 55%,#d9cfbd)" role="img" aria-label="Photo of a resort pool with palm trees by the beach"></div>
<svg class="abs" style="left:318px;top:2808px" width="248" height="62"><polygon points="0,22 248,0 248,62 0,62" fill="#fff"/></svg>
<div class="abs proj-label" style="left:318px;top:2842px;width:248px">Resort &amp; Hospitality</div>

<div class="abs" style="left:607px;top:2535px;width:287px;height:255px;background:linear-gradient(180deg,#8a5a3a,#d48a4a 35%,#2f4c63 70%,#1c3346)" role="img" aria-label="Photo of a rooftop infinity edge pool at dusk"></div>
<svg class="abs" style="left:624px;top:2730px" width="250" height="94"><polygon points="0,24 250,0 250,94 0,94" fill="#fff"/></svg>
<div class="abs proj-label" style="left:624px;top:2763px;width:250px">Infinity Edge<br>Designs</div>

<div class="abs" style="left:912px;top:2615px;width:287px;height:255px;background:linear-gradient(180deg,#dfe6ea,#b9ccd6 50%,#4aa8c7)" role="img" aria-label="Photo of an indoor architectural pool under a lattice roof"></div>
<svg class="abs" style="left:932px;top:2814px" width="246" height="90"><polygon points="0,22 246,0 246,90 0,90" fill="#fff"/></svg>
<div class="abs proj-label" style="left:932px;top:2848px;width:246px">Modern<br>Architectural Pools</div>

<div class="abs" style="left:550px;top:2942px;width:26px;height:3px;background:var(--blue)"></div>
<div class="abs" style="left:585px;top:2942px;width:26px;height:3px;background:#cfd6dd"></div>
<div class="abs" style="left:620px;top:2942px;width:26px;height:3px;background:#cfd6dd"></div>

<!-- testimonials -->
<div class="abs center eyebrow" style="top:3030px">Our Testimonials</div>
<h2 class="abs center head" style="top:3056px;font-size:37px">WHAT OUR CLIENTS SAY</h2>

<svg class="abs arrow" style="left:34px;top:3260px" viewBox="0 0 36 36" fill="none" stroke="#1d72d0" stroke-width="2"><circle cx="18" cy="18" r="16"/><path d="M26 18H11M17 12l-6 6 6 6"/></svg>
<svg class="abs arrow" style="left:1128px;top:3260px" viewBox="0 0 36 36" fill="none" stroke="#1d72d0" stroke-width="2"><circle cx="18" cy="18" r="16"/><path d="M10 18h15M19 12l6 6-6 6"/></svg>

<div class="abs quote" style="left:173px;top:3136px;width:403px;height:276px"></div>
<div class="abs avatar" style="left:108px;top:3205px;background:linear-gradient(180deg,#e4e8ec,#9fb6c9)" role="img" aria-label="Portrait photo of client Daniel"></div>
<div class="abs q-name" style="left:266px;top:3180px">Daniel</div>
<p class="abs q-text" style="left:266px;top:3218px">Lorem Ipsum is simply dummy text of the printing and typesetting industry. Lorem Ipsum has been the industry's standard dummy text ever since the 1500s, when an unknown printer took a galley of type and scrambled it to make a type</p>

<div class="abs quote" style="left:677px;top:3136px;width:403px;height:276px"></div>
<div class="abs avatar" style="left:612px;top:3205px;background:linear-gradient(180deg,#e8e8ea,#7a7a80)" role="img" aria-label="Portrait photo of client Sofia"></div>
<div class="abs q-name" style="left:770px;top:3180px">Sofia</div>
<p class="abs q-text" style="left:770px;top:3218px">Lorem Ipsum is simply dummy text of the printing and typesetting industry. Lorem Ipsum has been the industry's standard dummy text ever since the 1500s, when an unknown printer took a galley of type and scrambled it to make a type</p>

<!-- call to action -->
<svg class="abs" style="left:0;top:3497px" width="1200" height="380" viewBox="0 0 1200 380" preserveAspectRatio="none">
  <path d="M0 30 C80 10 160 40 260 42 C400 44 460 10 600 18 C740 26 800 50 940 40 C1060 30 1130 4 1200 10 L1200 348 C1100 372 1020 340 900 350 C760 362 700 330 560 340 C420 350 360 372 220 360 C120 352 60 372 0 378Z" fill="#10396a"/>
</svg>
<div class="abs" style="left:121px;top:3641px;font-size:16px;font-weight:600;color:var(--green)">Get in Touch</div>
<h2 class="abs head" style="left:118px;top:3670px;font-size:36px;color:var(--white)">LET’S CREATE YOUR PRIVATE PARADISE</h2>
<div class="abs btn btn-yellow" style="left:917px;top:3672px;width:162px;height:42px">GET A QUOTE</div>

<!-- footer -->
<div class="abs" style="left:197px;top:3935px;width:100px;height:100px;border-radius:50%;background:var(--blue)"></div>
<div class="abs" style="left:107px;top:4046px;width:280px;text-align:center;font-family:'Ubuntu',sans-serif;font-weight:500;font-size:23px;color:var(--navy)">CORAL BASINS</div>
<div class="abs" style="left:107px;top:4077px;width:280px;text-align:center;font-size:11.5px;font-weight:500;color:var(--navy)">ALL YOUR DREAMS COME TRUE</div>

<div class="abs f-head" style="left:408px;top:3920px">MAIN LINKS</div>
<ul class="abs f-list" style="left:408px;top:3952px">
  <li><svg width="12" height="12" viewBox="0 0 12 12"><path d="M1 6h9M6 2l4 4-4 4" stroke="#3a4450" stroke-width="1.8" fill="none"/></svg>Home</li>
  <li><svg width="12" height="12" viewBox="0 0 12 12"><path d="M1 6h9M6 2l4 4-4 4" stroke="#3a4450" stroke-width="1.8" fill="none"/></svg>About</li>
  <li><svg width="12" height="12" viewBox="0 0 12 12"><path d="M1 6h9M6 2l4 4-4 4" stroke="#3a4450" stroke-width="1.8" fill="none"/></svg>Services</li>
  <li><svg width="12" height="12" viewBox="0 0 12 12"><path d="M1 6h9M6 2l4 4-4 4" stroke="#3a4450" stroke-width="1.8" fill="none"/></svg>Who we serve</li>
  <li><svg width="12" height="12" viewBox="0 0 12 12"><path d="M1 6h9M6 2l4 4-4 4" stroke="#3a4450" stroke-width="1.8" fill="none"/></svg>Contact</li>
</ul>

<div class="abs f-head" style="left:604px;top:3920px">CONTACT US</div>
<svg class="abs" style="left:601px;top:3960px" width="34" height="34" viewBox="0 0 34 34" fill="none" stroke="#0d2c54" stroke-width="2"><circle cx="17" cy="17" r="15"/><path d="M17 26s-6-6-6-10a6 6 0 0 1 12 0c0 4-6 10-6 10z"/><circle cx="17" cy="16" r="2"/></svg>
<div class="abs f-contact" style="left:643px;top:3960px">Coral Basins<br>United States</div>
<svg class="abs" style="left:601px;top:4025px" width="34" height="34" viewBox="0 0 34 34" fill="none" stroke="#0d2c54" stroke-width="2"><circle cx="17" cy="17" r="15"/><path d="M11 11c-1 2 0 6 4 10s8 5 10 4l1-3-3-2-2 2c-2-1-4-3-5-5l2-2-2-3z"/></svg>
<div class="abs f-contact" style="left:643px;top:4029px">+1 555 014 2290</div>
<svg class="abs" style="left:601px;top:4076px" width="34" height="34" viewBox="0 0 34 34" fill="none" stroke="#0d2c54" stroke-width="2"><circle cx="17" cy="17" r="15"/><rect x="9" y="11" width="16" height="12" rx="1"/><path d="M9 12l8 6 8-6"/></svg>
<div class="abs f-contact" style="left:643px;top:4080px">info@coralbasins.com</div>

<div class="abs f-head" style="left:845px;top:3920px">NEWSLETTER SIGNUP</div>
<p class="abs" style="left:852px;top:3962px;font-size:11.5px;line-height:24px;color:var(--muted)">We Will Notify You Of Any<br>Important News</p>
<div class="abs" style="left:846px;top:4030px;width:204px;height:40px;border:1.5px solid #0d2c54;border-radius:6px"></div>
<div class="abs" style="left:856px;top:4043px;font-size:11.5px;color:var(--muted)">Your Email Address</div>
<div class="abs" style="left:1004px;top:4034px;width:42px;height:32px;border-radius:5px;background:var(--sky)"></div>
<svg class="abs" style="left:1014px;top:4039px" width="22" height="22" viewBox="0 0 22 22" fill="none" stroke="#fff" stroke-width="1.8" stroke-linejoin="round"><path d="M2 10l18-8-6 18-3-8z"/><path d="M11 12l9-10"/></svg>

<div class="abs" style="left:119px;top:4162px;width:955px;height:1.5px;background:#3a4450"></div>
<div class="abs center" style="top:4184px;font-size:12px;color:var(--text)">© 2025 Coral Basins I All Rights Reserved</div>

</body>
</html>
```